Need business card with a logo for a hearing aid sales and audiology business. We have two Hearing Instrument Specialists and one Audiologist on staff. Over 25 years in business. Locally owned and operated. Financing available. Most insurances accepted.

Summit Audio Wellness LLC
48730 W Larchmont, Suite 7
Spokane, WA 99281
509-617-2084
www.summitaudiowell.example

Manager
Tobias Kerrell HIS COHC
License #71829046

Target Market(s)

50yr old + people with a hearing loss.

Industry/Entity Type

Business

Contact Information for Business Card

48730 W Larchmont, Suite 7
Spokane, WA 99281
509-617-2084
www.summitaudiowell.example

Manager
Tobias Kerrell HIS COHC
NLVE #71829046

Font styles to use
Serif
Sans Serif

Requirements
Must have
• Business name, Tobias's name and title(s) and contact information, License #, web address

```html
<!DOCTYPE html>
<html lang="en">
<head>
<meta charset="utf-8">
<title>Summit Audio Wellness – Business Card</title>
<link rel="stylesheet" href="https://fonts.googleapis.com/css2?family=Ubuntu:wght@400&family=Questrial&display=swap">
<style>
  :root {
    --blue: #5b8dc0;
    --blue-text: #4a7fb8;
    --orange: #eea63a;
    --green: #a6cf5f;
    --white: #ffffff;
    --page: #e9e6e1;
  }
  html, body {
    margin: 0;
    padding: 0;
    width: 1200px;
    height: 813px;
    overflow: hidden;
    background: var(--page);
  }
  .card {
    position: absolute;
    left: 50px;
    top: 93px;
    width: 1074px;
    height: 612px;
    transform: scale(1.0242);
    transform-origin: top left;
    background: var(--white);
    box-shadow: 0 4px 14px rgba(0,0,0,0.18);
    overflow: hidden;
  }
  .person {
    position: absolute;
    right: 22px;
    top: 52px;
    width: 520px;
    text-align: center;
    font-family: "Ubuntu", sans-serif;
  }
  .person-name {
    display: block;
    text-align: right;
    font-size: 41px;
    color: var(--blue-text);
    line-height: 1.1;
  }
  .person-title {
    display: block;
    margin-left: 90px;
    font-size: 31px;
    color: var(--orange);
    line-height: 1.1;
  }
  .person-license {
    display: block;
    margin-left: 90px;
    font-size: 24px;
    font-style: italic;
    color: var(--green);
    line-height: 1.2;
  }
  .brand {
    position: absolute;
    left: 58px;
    top: 210px;
    display: flex;
    align-items: center;
    gap: 16px;
  }
  .brand-dot {
    width: 34px;
    height: 34px;
    border-radius: 50%;
    background: var(--orange);
    flex: none;
  }
  .brand-name {
    font-family: "Ubuntu", sans-serif;
    font-size: 36px;
    color: var(--blue-text);
    line-height: 1.15;
    width: 420px;
  }
  .contacts {
    position: absolute;
    left: 600px;
    top: 380px;
    margin: 0;
    padding: 0;
    list-style: none;
    font-family: "Questrial", sans-serif;
    font-size: 29px;
    color: var(--blue-text);
  }
  .contact {
    display: flex;
    align-items: center;
    gap: 16px;
    height: 35px;
  }
  .contact-icon { width: 32px; height: 30px; flex: none; }
  .contact-email { font-size: 25px; }
  .bands {
    position: absolute;
    left: 0;
    bottom: 0;
    width: 1074px;
    height: 99px;
  }
  .address {
    position: absolute;
    left: 0;
    width: 472px;
    top: 524px;
    text-align: center;
    font-family: "Questrial", sans-serif;
    font-size: 27px;
    line-height: 33px;
    color: var(--white);
  }
</style>
</head>
<body>
  <div class="card">
    <div class="brand">
      <span class="brand-dot"></span>
      <span class="brand-name">Summit Audio Wellness LLC</span>
    </div>

    <div class="person">
      <span class="person-name">Tobias Kerrell HIS COHC</span>
      <span class="person-title">Manager</span>
      <span class="person-license">NLVE #71829046</span>
    </div>

    <ul class="contacts">
      <li class="contact">
        <svg class="contact-icon" viewBox="0 0 32 30" aria-hidden="true">
          <circle cx="16" cy="15" r="14" fill="var(--orange)"/>
          <path d="M11 8c1-1 2-1 3 0l2 3c.5 1 0 2-1 2.5-.5.5 0 2 1.5 3.5s3 2 3.5 1.5c.5-1 1.5-1.5 2.5-1l3 2c1 1 1 2 0 3-2 2-5 2-9-2s-5-8-5.5-10z" fill="var(--white)"/>
        </svg>
        <span>509-617-2084</span>
      </li>
      <li class="contact">
        <svg class="contact-icon" viewBox="0 0 32 30" aria-hidden="true">
          <rect x="3" y="7" width="26" height="17" fill="var(--orange)"/>
          <path d="M3 7l13 10 13-10" fill="none" stroke="var(--white)" stroke-width="2"/>
        </svg>
        <span class="contact-email">tobias@summitaudiowell.example</span>
      </li>
      <li class="contact">
        <svg class="contact-icon" viewBox="0 0 32 30" aria-hidden="true">
          <g fill="none" stroke="var(--orange)" stroke-width="2">
            <circle cx="16" cy="15" r="13"/>
            <ellipse cx="16" cy="15" rx="6" ry="13"/>
            <path d="M3 15h26M5 8h22M5 22h22M16 2v26"/>
          </g>
        </svg>
        <span>www.summitaudiowell.example</span>
      </li>
    </ul>

    <svg class="bands" viewBox="0 0 1074 99" aria-hidden="true">
      <polygon points="0,0 480,0 512,47 1074,47 1074,99 0,99" fill="var(--blue)"/>
      <polygon points="496,0 1074,0 1074,36 520,36" fill="var(--green)"/>
    </svg>

    <div class="address">
      48730 W Larchmont, Suite 7<br>
      Spokane, WA 99281
    </div>
  </div>
</body>
</html>
```